Create a business promotion flyer to leave in customer mailboxes. We are a bulk petroleum supplier, servicing any industry that requires diesel. Base in griffith NSW, servicing griffith area and surrounds.

Business Name - Terra Diesel
Fuel@terradiesel-example.com.au
Owen - 0491 570 362 ohartley@terradiesel-example.com.au
Liam - 0491 570 718 lprosser@terradiesel-example.com.au
Simon - 0491 570 905 skenway@terradiesel-example.com.au
Office 02 5550 1734

Bulk Fuel deliveries.
Oils & lubricants
Local Family owned business

```html
<!DOCTYPE html>
<html lang="en">
<head>
<meta charset="utf-8">
<title>Terra Diesel – Bulk Fuel Flyer</title>
<link rel="stylesheet" href="https://fonts.googleapis.com/css2?family=Poppins:wght@400;500;600;700;800&display=swap">
<style>
:root{
  --red:#ed1c24;
  --ink:#231f20;
  --panel:#231f20;
  --backdrop:#58595b;
  --sky-light:#e8f5fd;
  --white:#ffffff;
}
*{margin:0;padding:0;box-sizing:border-box}
html,body{width:1051px;height:1200px;overflow:hidden;background:var(--backdrop)}
body{font-family:"Poppins",sans-serif;color:var(--ink);position:relative}
.flyer{position:absolute;left:174px;top:154px;width:702px;height:909px;overflow:hidden;background:var(--sky-light)}
.flyer *{position:absolute}
.hero-photo{left:140px;top:0;width:562px;height:300px;
  background:linear-gradient(180deg,#5d8fc9 0%,#b9d3ec 35%,#d7dde3 55%,#a9adb2 75%,#e4e6e8 100%);
  -webkit-mask-image:linear-gradient(90deg,transparent 0%,#000 35%);
  mask-image:linear-gradient(90deg,transparent 0%,#000 35%)}
.shapes{left:0;top:0;width:702px;height:909px}
.tagline-box{left:520px;top:0;width:150px;height:183px;background:var(--red);color:var(--white);
  font-size:16px;line-height:20px;text-align:center;padding-top:45px}
.tagline-box b{position:static;font-weight:700}
.tagline-box span{position:static;display:block}
.brand-name{left:54px;top:70px;font-size:33px;font-weight:600;color:var(--red);letter-spacing:-.3px}
.headline{left:48px;top:156px;font-size:47px;font-weight:800;line-height:47px;letter-spacing:-.5px;color:var(--ink)}
.headline span{position:static;display:block}
.headline .accent{color:var(--red)}
.services-title{left:77px;top:480px;font-size:28px;font-weight:400}
.service-icon{left:72px;width:60px;height:60px;border-radius:50%;background:var(--red)}
.service-icon svg{left:14px;top:14px;width:32px;height:32px}
.service-name{left:154px;font-size:21px;font-weight:700;line-height:26px;text-transform:uppercase}
.service-desc{left:156px;font-size:13px;line-height:15px;font-weight:400}
.contact-panel{left:415px;top:372px;width:287px;height:478px;background:var(--panel);color:var(--white)}
.panel-heading{left:22px;top:25px;font-size:27px;font-weight:600;line-height:36px;width:260px;white-space:nowrap}
.contact{left:0;width:287px;height:70px}
.contact svg{left:30px;width:11px;height:11px;fill:var(--white)}
.contact .name{left:51px;top:0;font-size:19px;font-weight:500}
.contact .phone{left:51px;top:22px;font-size:19px;font-weight:600}
.contact .email{left:51px;top:49px;font-size:10.5px;font-weight:400;white-space:nowrap;max-width:226px}
.footer{left:0;top:856px;width:702px;height:53px;background:var(--red);color:var(--white)}
.footer .ask{left:78px;top:16px;font-size:15px}
.footer svg{left:306px;top:21px;width:13px;height:10px;fill:var(--white)}
.footer .mail{left:330px;top:13px;font-size:17px;font-weight:700}
</style>
</head>
<body>
<main class="flyer">
  <div class="hero-photo" role="img" aria-label="Photo of fuel tanker road trains parked in front of a depot shed under a blue sky"></div>

  <svg class="shapes" viewBox="0 0 702 909" aria-hidden="true">
    <defs>
      <linearGradient id="lower-fill" x1="0" x2="1" y1="0" y2="0">
        <stop offset="0" stop-color="#e6e7e9"/>
        <stop offset="0.6" stop-color="#ffffff"/>
      </linearGradient>
    </defs>
    <path d="M0 482 Q300 360 702 358 L702 909 L0 909 Z" fill="url(#lower-fill)"/>
    <path d="M46 460 Q330 318 702 288 L702 350 Q380 352 46 460 Z" fill="var(--red)"/>
  </svg>

  <div class="tagline-box">
    <span>Reliable bulk</span>
    <span>fuel supply</span>
    <span>across <b>Griffith</b></span>
    <span>and surrounds</span>
  </div>

  <div class="brand-name">Terra Diesel</div>

  <h1 class="headline">
    <span class="accent">FUEL FOR</span>
    <span>FARMING,</span>
    <span>TRANSPORT</span>
    <span>&amp; INDUSTRY</span>
  </h1>

  <h2 class="services-title">Our Services</h2>

  <div class="service-icon" style="top:540px">
    <svg viewBox="0 0 32 32" fill="none" stroke="#fff" stroke-width="1.5"><rect x="6" y="4" width="14" height="24" rx="1"/><rect x="9" y="7" width="8" height="5"/><path d="M13 15c-2 3-3 4-3 5.5a3 3 0 006 0c0-1.5-1-2.5-3-5.5z"/><path d="M20 10l4 3v11a2 2 0 004 0V12l-3-3"/><path d="M4 28h18"/></svg>
  </div>
  <div class="service-name" style="top:533px">Bulk Fuel<br>Deliveries.</div>
  <div class="service-desc" style="top:587px">Reliable diesel supply<br>for any industry.</div>

  <div class="service-icon" style="top:646px">
    <svg viewBox="0 0 32 32" fill="none" stroke="#fff" stroke-width="1.5"><path d="M9 9h15a2 2 0 012 2v16a1 1 0 01-1 1H9a1 1 0 01-1-1V10z"/><path d="M9 9L6 5l3-2 4 5"/><path d="M14 15c-1.5 2.5-2.5 3.5-2.5 4.5a2.5 2.5 0 005 0c0-1-1-2-2.5-4.5z"/><rect x="19" y="14" width="3" height="6" rx="1.5"/><path d="M10 24h14M10 26h14"/></svg>
  </div>
  <div class="service-name" style="top:636px">Oils &amp;<br>Lubricants</div>
  <div class="service-desc" style="top:689px">Quality products to keep your<br>equipment performing at its best.</div>

  <div class="service-icon" style="top:751px">
    <svg viewBox="0 0 32 32" fill="none" stroke="#fff" stroke-width="1.5"><circle cx="8" cy="10" r="3"/><circle cx="16" cy="8" r="3"/><circle cx="24" cy="10" r="3"/><path d="M3 22v-3a4 4 0 018 0M11 24v-5a5 5 0 0110 0v5M21 22v-3a4 4 0 018 0"/></svg>
  </div>
  <div class="service-name" style="top:742px">Local Family<br>Owned Business</div>
  <div class="service-desc" style="top:797px">Proudly supporting our<br>local community.</div>

  <section class="contact-panel">
    <h2 class="panel-heading">Need fuel for<br>your operation?</h2>

    <div class="contact" style="top:129px">
      <svg style="top:5px" viewBox="0 0 12 12"><circle cx="6" cy="3.5" r="3"/><path d="M0 12c0-4 2.5-5 6-5s6 1 6 5z"/></svg>
      <svg style="top:28px" viewBox="0 0 12 12"><path d="M3 0l2 3-1.5 1.5c.5 1.5 2 3 3.5 3.5L8.5 6.5l3 2L10 12C5 11 1 7 0 2z"/></svg>
      <svg style="top:53px" viewBox="0 0 12 12"><path d="M0 2h12v1L6 7 0 3zM0 4.5l6 4 6-4V10H0z"/></svg>
      <div class="name">Owen</div>
      <div class="phone">0491 570 362</div>
      <div class="email">ohartley@terradiesel-example.com.au</div>
    </div>

    <div class="contact" style="top:225px">
      <svg style="top:5px" viewBox="0 0 12 12"><circle cx="6" cy="3.5" r="3"/><path d="M0 12c0-4 2.5-5 6-5s6 1 6 5z"/></svg>
      <svg style="top:28px" viewBox="0 0 12 12"><path d="M3 0l2 3-1.5 1.5c.5 1.5 2 3 3.5 3.5L8.5 6.5l3 2L10 12C5 11 1 7 0 2z"/></svg>
      <svg style="top:53px" viewBox="0 0 12 12"><path d="M0 2h12v1L6 7 0 3zM0 4.5l6 4 6-4V10H0z"/></svg>
      <div class="name">Liam</div>
      <div class="phone">0491 570 718</div>
      <div class="email">lprosser@terradiesel-example.com.au</div>
    </div>

    <div class="contact" style="top:320px">
      <svg style="top:5px" viewBox="0 0 12 12"><circle cx="6" cy="3.5" r="3"/><path d="M0 12c0-4 2.5-5 6-5s6 1 6 5z"/></svg>
      <svg style="top:28px" viewBox="0 0 12 12"><path d="M3 0l2 3-1.5 1.5c.5 1.5 2 3 3.5 3.5L8.5 6.5l3 2L10 12C5 11 1 7 0 2z"/></svg>
      <svg style="top:53px" viewBox="0 0 12 12"><path d="M0 2h12v1L6 7 0 3zM0 4.5l6 4 6-4V10H0z"/></svg>
      <div class="name">Simon</div>
      <div class="phone">0491 570 905</div>
      <div class="email">skenway@terradiesel-example.com.au</div>
    </div>

    <div class="contact" style="top:416px">
      <svg style="top:4px;left:26px;width:16px;height:14px" viewBox="0 0 16 14" fill="none" stroke="#fff" stroke-width="1"><rect x="1" y="5" width="6" height="8.5"/><rect x="7" y="1" width="8" height="12.5"/><path d="M3 7h2M3 9h2M9 3h1M12 3h1M9 6h1M12 6h1M9 9h1M12 9h1"/></svg>
      <svg style="top:28px" viewBox="0 0 12 12"><path d="M3 0l2 3-1.5 1.5c.5 1.5 2 3 3.5 3.5L8.5 6.5l3 2L10 12C5 11 1 7 0 2z"/></svg>
      <div class="name">Office</div>
      <div class="phone">02 5550 1734</div>
    </div>
  </section>

  <footer class="footer">
    <div class="ask">Have questions? Email us at:</div>
    <svg viewBox="0 0 12 10"><path d="M0 0h12v1L6 5 0 1zM0 2.5l6 4 6-4V10H0z"/></svg>
    <div class="mail">Fuel@terradiesel-example.com.au</div>
  </footer>
</main>
</body>
</html>
```